Information One Page for Email

I am looking for a informative attachment I can send with an introductive email for Meridale Slab Works. Something I can also Mail.

Meridale Slab Works is the leader in Rebar Post Tension Cable Placement and Post Tension Cable repair. Outside of cable placement and repair we do concrete repair, Parking Garage restoration and
Updates

Content

Post Tension Repair and Concrete Restoration
Post-tensioning is a revolutionary method in concrete construction that enhances the strength and durability of structures. However, like all construction ele-ments, post-tension cables can experience wear and damage over time. Ensuring timely and effective repair is crucial for maintaining the safety and integrity of your building.
Why Post-Tension Cable Repair is Essential
1. **Structural Integrity**: Damaged or deteriorated cables can compromise the structural integrity of your building, leading to safety hazards and potential structural failures.
2. **Extended Lifespan**: Regular maintenance and repair of post-tension cables extend the lifespan of your structure, ensuring it remains safe and function-al for years to come.
3. **Cost-Effective**: Addressing cable issues early on prevents more severe damage and costly repairs down the line.
Common Signs of Post-Tension Cable Issues
- Cracks in concrete surfaces
- Unusual noises or popping sounds
- Visible cable ends or broken strands
- Water leakage through cracks
Our Repair Process
1. **Inspection and Assessment**: Our team conducts a thorough inspection to identify the extent of the damage and determine the appropriate repair meth-ods.
2. **Cable Repair or Replacement**: Depending on the severity, we either re-pair the existing cables or replace them with new ones to restore full functional-ity.
3. **Sealing and Protection**: After repairing, we seal the affected areas to protect against moisture and future damage.
4. **Quality Assurance**: We perform rigorous quality checks to ensure the repairs meet industry standards and the structure is safe for use.
Why Choose Us
- **Expertise and Experience**: With years of experience in post-tension cable repair, our team is skilled in handling even the most complex repairs efficiently and effectively.
- **Advanced Technology**: We use the latest technology and materials to ensure durable and long-lasting repairs.
- **Customer Satisfaction**: Our commitment to quality and customer satisfaction sets us apart. We work closely with our clients to ensure their needs are met and expectations exceeded.
Contact Us
If you suspect issues with your post-tension cables or need a routine inspection, don't hesitate to contact us. Our experts are ready to provide the best solutions to keep your structures safe and secure.
Ensure the safety and longevity of your building with our professional post-tension cable repair services. Trust us to deliver quality and reliability every time.

```html
<!DOCTYPE html>
<html lang="en">
<head>
<meta charset="utf-8">
<title>Meridale Slab Works – Post Tension Repair &amp; Concrete Restoration</title>
<link href="https://fonts.googleapis.com/css2?family=Poppins:wght@400;500;600;700;800&display=swap" rel="stylesheet">
<style>
:root{
  --green:#0a6b34;
  --green-dark:#075a2b;
  --green-text:#0c7439;
  --ink:#111;
  --body:#222;
  --band:#e3e3e3;
  --footer:#3d3d3d;
  --page:#9a9a9a;
  --white:#fff;
}
*{box-sizing:border-box;margin:0;padding:0}
html,body{width:745px;height:1200px;overflow:hidden}
body{background:var(--page);font-family:'Poppins',sans-serif;color:var(--body)}
.sheet{position:absolute;left:62px;top:0;width:621px;height:1200px;background:var(--white);overflow:hidden}
.abs{position:absolute}
.brand{left:33px;top:36px;display:flex;align-items:center;gap:8px}
.brand-mark{width:14px;height:14px;background:var(--green)}
.brand-name{font-weight:700;color:var(--green);font-size:20px;line-height:22px}
.hero-shape{left:0;top:0}
.hero-title{left:32px;top:166px;color:var(--white);font-weight:800;font-size:34px;line-height:34.5px;letter-spacing:-.3px}
.hero-text{left:32px;top:315px;width:325px;color:var(--white);font-size:9.3px;line-height:11.6px}
.photo{border:3px solid var(--white);left:375px;width:214px}
.photo-slab{top:33px;height:170px;background:linear-gradient(160deg,#6c9ab8,#8a6b5a 60%,#7a5c4c)}
.photo-balcony{top:209px;height:171px;background:linear-gradient(180deg,#d8d4cc,#8e8a84 55%,#c9c3b8)}
.sec-head{font-weight:700;font-size:13.2px;line-height:15px;color:var(--ink);text-transform:uppercase}
.sec-head span{color:var(--green-text)}
.why-head{left:32px;top:407px}
.signs-head{left:373px;top:407px}
.icon-circle{width:52px;height:52px;border-radius:50%;background:var(--green);display:flex;align-items:center;justify-content:center}
.timeline{left:97.5px;top:453px;width:1px;height:181px;background:var(--ink)}
.dot{width:5px;height:5px;border-radius:50%;background:var(--ink);left:95.5px}
.benefit{left:114px;width:212px}
.benefit h3{font-size:12.5px;line-height:14px;font-weight:700;color:var(--green-text);margin-bottom:3px}
.benefit p{font-size:8.2px;line-height:10px;color:var(--body)}
.rule{left:114px;width:176px;height:1px;background:#999}
.sign{font-size:8.3px;line-height:10px;color:var(--body);padding-left:9px;width:90px}
.sign::before{content:"";position:absolute;left:0;top:2px;width:6px;height:6px;border-radius:50%;background:var(--green)}
.photo-site{left:374px;top:518px;width:214px;height:115px}
.band{left:0;top:765px;width:621px;height:124px;background:var(--band)}
.pill{height:31px;background:var(--ink);color:var(--white);font-weight:700;font-size:12.6px;display:flex;align-items:center;justify-content:center;clip-path:polygon(7% 0,100% 0,93% 100%,0 100%)}
.step-num{font-weight:700;font-size:20px;width:60px;text-align:center;color:var(--ink)}
.step{text-align:center}
.step h3{font-size:12px;line-height:14px;font-weight:700;color:var(--green-text);margin-bottom:3px;white-space:nowrap}
.step p{font-size:8.2px;line-height:10px}
.feature{text-align:center}
.feature h3{font-size:12.4px;line-height:14px;font-weight:700;color:var(--green-text);margin-bottom:4px;white-space:nowrap}
.feature p{font-size:8.2px;line-height:10px;margin:0 auto}
.vrule{width:1px;height:98px;background:#aaa;top:956px}
.footer{left:0;top:1069px;width:621px;height:131px;background:var(--footer);color:var(--white)}
.footer p{position:absolute;left:36px;width:549px;text-align:center;font-size:8.2px;line-height:10px}
.contact-bar{position:absolute;left:33px;top:1141px;width:365px;height:23px;border-radius:12px;background:var(--green);display:flex;align-items:center}
.contact-label{background:var(--white);color:var(--green);font-weight:700;font-size:15px;height:23px;width:98px;border-radius:12px;display:flex;align-items:center;justify-content:center}
.contact-item{display:flex;align-items:center;gap:4px;font-size:9px;margin-left:7px;color:var(--white)}
.follow{position:absolute;left:475px;top:1146px;display:flex;align-items:center;gap:5px;font-size:9.5px;font-weight:700;color:var(--white)}
.social{width:12px;height:12px;border-radius:50%;background:var(--white)}
</style>
</head>
<body>
<div class="sheet">
  <div class="abs brand"><span class="brand-mark"></span><div class="brand-name">Meridale<br>Slab Works<br>LLC</div></div>

  <svg class="abs hero-shape" width="621" height="400" viewBox="0 0 621 400">
    <polyline points="0,135 308,135 374,206" fill="none" stroke="#111" stroke-width="0.8"/>
    <polygon points="0,146 303,146 374,216 374,253 621,253 621,391 0,391" fill="var(--green)"/>
    <line x1="589" y1="243" x2="621" y2="243" stroke="#111" stroke-width="0.8"/>
  </svg>

  <h1 class="abs hero-title">POST TENSION<br>REPAIR &amp;<br>CONCRETE<br>RESTORATION</h1>
  <p class="abs hero-text">Post-tensioning is a revolutionary method in concrete construction that enhances the strength and durability of structures. However, like all construction ele-ments, post-tension cables can experience wear and damage over time. Ensuring timely and effective repair is crucial for maintaining the safety and integrity of your building.</p>

  <div class="abs photo photo-slab" role="img" aria-label="Blue post-tension cables laid across a slab deck before the pour"></div>
  <div class="abs photo photo-balcony" role="img" aria-label="Worker breaking out a damaged concrete balcony slab supported by shoring posts"></div>

  <h2 class="abs sec-head why-head">Why <span>Post-Tension Cable<br>Repair is Essential</span></h2>
  <h2 class="abs sec-head signs-head">Common Signs of<br><span>Post-Tension Cable Issues</span></h2>

  <div class="abs icon-circle" style="left:32px;top:448px">
    <svg width="28" height="28" viewBox="0 0 28 28" fill="#fff"><rect x="3" y="12" width="3" height="8"/><rect x="8" y="8" width="3" height="12"/><rect x="13" y="5" width="3" height="15"/><circle cx="21" cy="20" r="5" fill="none" stroke="#fff" stroke-width="2"/><rect x="3" y="22" width="12" height="2"/></svg>
  </div>
  <div class="abs icon-circle" style="left:32px;top:522px">
    <svg width="28" height="28" viewBox="0 0 28 28" fill="none" stroke="#fff" stroke-width="2"><path d="M5 14a9 9 0 0 1 15-7"/><path d="M23 14a9 9 0 0 1-15 7"/><path d="M20 3v4h-4M8 25v-4h4"/><rect x="10" y="10" width="8" height="8"/></svg>
  </div>
  <div class="abs icon-circle" style="left:32px;top:593px">
    <svg width="28" height="28" viewBox="0 0 28 28" fill="#fff"><rect x="4" y="16" width="3" height="8"/><rect x="9" y="12" width="3" height="12"/><path d="M13 9l4-5 4 5h-3v4h-2V9z"/><circle cx="20" cy="19" r="5"/></svg>
  </div>

  <div class="abs timeline"></div>
  <span class="abs dot" style="top:451px"></span>
  <span class="abs dot" style="top:627px"></span>
  <span class="abs dot" style="top:545px"></span>

  <div class="abs benefit" style="top:451px"><h3>Structural Integrity</h3><p>Damaged or deteriorated cables can compromise the structural integrity of your building, leading to safety hazards and potential structural failures.</p></div>
  <div class="abs rule" style="top:510px"></div>
  <div class="abs benefit" style="top:521px"><h3>Extended Lifespan</h3><p>Regular maintenance and repair of post-tension cables extend the lifespan of your structure, ensuring it remains safe and function-al for years to come.</p></div>
  <div class="abs rule" style="top:586px"></div>
  <div class="abs benefit" style="top:598px"><h3>Cost-Effective</h3><p>Addressing cable issues early on prevents more severe damage and costly repairs down the line.</p></div>

  <div class="abs sign" style="left:374px;top:459px">Cracks in concrete surfaces</div>
  <div class="abs sign" style="left:477px;top:459px">Visible cable ends or broken strands</div>
  <div class="abs sign" style="left:374px;top:489px">Unusual noises or popping sounds</div>
  <div class="abs sign" style="left:477px;top:489px">Water leakage through cracks</div>

  <svg class="abs photo-site" width="214" height="115" viewBox="0 0 214 115" role="img" aria-label="Multi-storey building under construction beside a dirt access road">
    <defs><linearGradient id="site" x1="0" y1="0" x2="0" y2="1"><stop offset="0" stop-color="#8e9498"/><stop offset=".55" stop-color="#6f6a62"/><stop offset="1" stop-color="#a89b86"/></linearGradient></defs>
    <polygon points="0,0 200,0 214,14 214,115 0,115" fill="url(#site)" stroke="var(--green)" stroke-width="2"/>
  </svg>

  <svg class="abs" style="left:0;top:650px" width="621" height="60" viewBox="0 0 621 60">
    <polyline points="32,35 32,18 180,18" fill="none" stroke="#555" stroke-width="0.8"/>
    <polyline points="411,18 587,18 587,35" fill="none" stroke="#555" stroke-width="0.8"/>
  </svg>
  <div class="abs pill" style="left:223px;top:653px;width:177px">OUR REPAIR PROCESS</div>

  <div class="abs band"></div>

  <div class="abs step-num" style="left:69px;top:693px">01</div>
  <div class="abs step-num" style="left:228px;top:693px">02</div>
  <div class="abs step-num" style="left:376px;top:693px">03</div>
  <div class="abs step-num" style="left:505px;top:693px">04</div>

  <svg class="abs" style="left:0;top:718px" width="621" height="85" viewBox="0 0 621 85">
    <g stroke="#111" stroke-width="0.8"><line x1="99" y1="0" x2="99" y2="15"/><line x1="258" y1="0" x2="258" y2="15"/><line x1="406" y1="0" x2="406" y2="15"/><line x1="535" y1="0" x2="535" y2="15"/></g>
    <g fill="var(--green)">
      <path d="M99 78l-9-9a28 28 0 1 1 18 0z"/><path d="M258 78l-9-9a28 28 0 1 1 18 0z"/><path d="M406 78l-9-9a28 28 0 1 1 18 0z"/><path d="M535 78l-9-9a28 28 0 1 1 18 0z"/>
    </g>
    <g fill="#fff"><circle cx="99" cy="45" r="23"/><circle cx="258" cy="45" r="23"/><circle cx="406" cy="45" r="23"/><circle cx="535" cy="45" r="23"/></g>
    <g fill="var(--green)">
      <circle cx="96" cy="40" r="5"/><path d="M86 55q2-9 10-9t10 9z"/><circle cx="107" cy="34" r="3.5"/>
      <path d="M250 55l6-10 4 3 6-10-4 0 2-4" fill="none" stroke="var(--green)" stroke-width="3"/>
      <path d="M406 32l10 4v8q0 8-10 12q-10-4-10-12v-8z" fill="none" stroke="var(--green)" stroke-width="2.5"/><path d="M401 44l4 4 6-7" fill="none" stroke="var(--green)" stroke-width="2.2"/>
      <circle cx="537" cy="36" r="4"/><path d="M524 52q6-6 12-3h6l-2 3h-6l14-4-6 8h-18z"/>
    </g>
    <g fill="var(--green)">
      <path d="M167 36h8l9 9-9 9h-8l9-9z"/><path d="M180 36h8l9 9-9 9h-8l9-9z"/>
      <path d="M322 36h8l9 9-9 9h-8l9-9z"/><path d="M335 36h8l9 9-9 9h-8l9-9z"/>
      <path d="M462 36h8l9 9-9 9h-8l9-9z"/><path d="M475 36h8l9 9-9 9h-8l9-9z"/>
    </g>
  </svg>

  <div class="abs step" style="left:31px;top:805px;width:136px"><h3>Inspection<br>&amp; Assessment</h3><p>Our team conducts a thorough inspection to identify the extent of the damage and determine the appropriate repair methods.</p></div>
  <div class="abs step" style="left:187px;top:804px;width:142px"><h3>Cable Repair<br>or Replacement</h3><p>Depending on the severity, we either re-pair the existing cables or replace them with new ones to restore full functional-ity.</p></div>
  <div class="abs step" style="left:347px;top:805px;width:116px"><h3>Sealing<br>&amp; Protection</h3><p>After repairing, we seal the affected areas to protect against moisture and future damage.</p></div>
  <div class="abs step" style="left:480px;top:805px;width:110px"><h3>Quality<br>Assurance</h3><p>We perform rigorous quality checks to ensure the repairs meet industry standards and the structure is safe for use.</p></div>

  <svg class="abs" style="left:0;top:915px" width="621" height="40" viewBox="0 0 621 40">
    <polyline points="33,32 33,6 232,6" fill="none" stroke="#555" stroke-width="0.8"/>
    <polyline points="392,6 589,6 589,32" fill="none" stroke="#555" stroke-width="0.8"/>
  </svg>
  <div class="abs pill" style="left:240px;top:905px;width:143px">WHY CHOOSE US</div>

  <div class="abs icon-circle" style="left:102px;top:947px;width:44px;height:44px">
    <svg width="26" height="26" viewBox="0 0 26 26" fill="#fff"><circle cx="7" cy="4" r="2"/><circle cx="13" cy="3" r="2"/><circle cx="19" cy="4" r="2"/><circle cx="8" cy="12" r="3"/><circle cx="18" cy="12" r="3"/><circle cx="13" cy="14" r="3"/><path d="M5 23q0-6 8-6t8 6z"/></svg>
  </div>
  <div class="abs icon-circle" style="left:290px;top:947px;width:44px;height:44px">
    <svg width="26" height="26" viewBox="0 0 26 26" fill="#fff"><circle cx="15" cy="8" r="4"/><path d="M3 20q5-5 10-3h6l-2 3h-5l11-3-5 6H4z"/></svg>
  </div>
  <div class="abs icon-circle" style="left:479px;top:947px;width:44px;height:44px">
    <svg width="26" height="26" viewBox="0 0 26 26" fill="#fff"><circle cx="13" cy="10" r="4"/><path d="M5 22q0-7 8-7t8 7z"/><circle cx="20" cy="19" r="4" fill="#fff" stroke="var(--green)" stroke-width="1.5"/><circle cx="5" cy="5" r="1.5"/><circle cx="13" cy="3" r="1.5"/><circle cx="21" cy="5" r="1.5"/></svg>
  </div>

  <div class="abs feature" style="left:33px;top:1004px;width:182px"><h3>Expertise &amp; Experience</h3><p style="width:180px">With years of experience in post-tension cable repair, our team is skilled in handling even the most complex repairs efficiently and effectively.</p></div>
  <div class="abs vrule" style="left:226px"></div>
  <div class="abs feature" style="left:236px;top:1003px;width:154px"><h3>Advanced Technology</h3><p style="width:142px">We use the latest technology and materials to ensure durable and long-lasting repairs.</p></div>
  <div class="abs vrule" style="left:400px"></div>
  <div class="abs feature" style="left:410px;top:1004px;width:182px"><h3>Customer Satisfaction</h3><p style="width:178px">Our commitment to quality and customer satisfaction sets us apart. We work closely with our clients to ensure their needs are met and expectations exceeded.</p></div>

  <footer class="abs footer">
    <p style="top:15px">If you suspect issues with your post-tension cables or need a routine inspection, don't hesitate to contact us. Our experts are ready to provide the best solutions to keep your structures safe and secure.</p>
    <p style="top:45px">Ensure the safety and longevity of your building with our professional post-tension cable repair services. Trust us to deliver quality and reliability every time.</p>
  </footer>
  <div class="contact-bar">
    <span class="contact-label">Contact Us</span>
    <span class="contact-item"><svg width="10" height="10" viewBox="0 0 10 10"><circle cx="5" cy="5" r="4.5" fill="none" stroke="#fff"/><path d="M3 2.5l1 1-0.5 1q0.7 1.3 2 2l1-0.5 1 1-1 1q-3 0-4.5-4.5z" fill="#fff"/></svg>(555) 214-0397</span>
    <span class="contact-item"><svg width="10" height="10" viewBox="0 0 10 10"><circle cx="5" cy="5" r="4.5" fill="#fff"/><rect x="2.5" y="3.3" width="5" height="3.4" fill="none" stroke="var(--green)" stroke-width="0.8"/><path d="M2.5 3.3l2.5 2 2.5-2" fill="none" stroke="var(--green)" stroke-width="0.8"/></svg>info@meridaleslab.com</span>
  </div>
  <div class="follow">FOLLOW US ON <span class="social"></span><span class="social"></span></div>
</div>
</body>
</html>
```